Web Developer Needs a Business Card Design

I need a personal business card design that represents me as a web developer for potential employers. I would like the background to be a dark color on the front for contrast with my logo and name. The back will have all my information along with a smaller version of the logo. I want something with a modern look and feel, not too conservative. This will be used for potential employers and freelance work.

Industry/Entity Type

Business

Contact Information for Business Card

Front should have my logo and name. The back should have all my personal information which would include: name: Tom Varulek, phone: 570-614-3098, email: tomvarulek@quillbox.net, website url: www.tomvarulek.net, logo, web developer.

Font styles to use
Sans Serif

Requirements
Must have
• Must include my logo. The color palette base color will be the logo color.

```html
<!DOCTYPE html>
<html lang="en">
<head>
<meta charset="utf-8">
<title>Tom Varulek — Business Card</title>
<link rel="stylesheet" href="https://fonts.googleapis.com/css2?family=Open+Sans:wght@400;600&display=swap">
<style>
  :root {
    --backdrop: #3f3431;
    --card: #0d0d0e;
    --card-edge: #1a1a1b;
    --accent: #4fe3c6;
    --silver: #a9a9a9;
    --text: #f2f2f2;
    --rule: #8a8a8a;
  }
  * { margin: 0; padding: 0; box-sizing: border-box; }
  html, body {
    width: 1200px; height: 839px; overflow: hidden;
    background: var(--backdrop);
    font-family: "Open Sans", sans-serif;
  }
  .stage {
    position: relative; width: 1200px; height: 839px;
    display: flex; align-items: center; justify-content: center; gap: 60px;
  }
  .card {
    position: relative; width: 520px; height: 298px;
    background: var(--card);
    border: 1px solid var(--card-edge);
    box-shadow: 0 14px 30px rgba(0,0,0,0.45);
  }
  /* Back side: contact details */
  .card-back .brand {
    position: absolute; left: 0; top: 0; width: 232px; height: 100%;
    display: flex; flex-direction: column; align-items: center; justify-content: center; gap: 14px;
  }
  .brand-ring {
    width: 96px; height: 96px; border-radius: 50%;
    border: 7px solid var(--accent);
  }
  .brand-name {
    color: var(--accent); font-weight: 600; font-size: 17px; letter-spacing: 0.3px;
  }
  .divider {
    position: absolute; left: 232px; top: 40px; width: 1px; height: 218px;
    background: var(--rule);
  }
  .identity { position: absolute; left: 258px; top: 44px; }
  .identity .name { color: var(--accent); font-weight: 600; font-size: 24px; line-height: 1.1; }
  .identity .role { color: var(--text); font-size: 12px; margin-top: 2px; }
  .contacts {
    position: absolute; left: 258px; top: 168px; list-style: none;
    display: flex; flex-direction: column; gap: 7px;
  }
  .contacts li { display: flex; align-items: center; gap: 10px; color: var(--text); font-size: 14px; }
  .contact-icon { width: 12px; height: 12px; flex: none; }
  /* Front side: logo and name */
  .card-front {
    display: flex; flex-direction: column; align-items: center; justify-content: center; gap: 14px;
  }
  .front-ring {
    width: 84px; height: 84px; border-radius: 50%;
    border: 5px solid var(--silver);
  }
  .front-name { color: var(--silver); font-weight: 600; font-size: 19px; letter-spacing: 0.4px; }
</style>
</head>
<body>
<main class="stage">
  <section class="card card-back" aria-label="Card back with contact details">
    <div class="brand">
      <div class="brand-ring"></div>
      <div class="brand-name">Tom Varulek</div>
    </div>
    <div class="divider"></div>
    <div class="identity">
      <div class="name">Tom Varulek</div>
      <div class="role">web developer</div>
    </div>
    <ul class="contacts">
      <li>
        <svg class="contact-icon" viewBox="0 0 12 12" aria-hidden="true"><rect width="12" height="12" rx="2" fill="#4fe3c6"/><path d="M3.5 3h1.5l.6 1.6-.9.7a4.5 4.5 0 0 0 2 2l.7-.9L9 7v1.5c0 .5-.4.8-.9.8A5.6 5.6 0 0 1 2.7 3.9c0-.5.3-.9.8-.9z" fill="#0d0d0e"/></svg>
        570-614-3098
      </li>
      <li>
        <svg class="contact-icon" viewBox="0 0 12 12" aria-hidden="true"><rect width="12" height="12" rx="2" fill="#4fe3c6"/><circle cx="6" cy="6" r="3" fill="none" stroke="#0d0d0e" stroke-width="1.1"/><path d="M3 6h6M6 3v6" stroke="#0d0d0e" stroke-width="0.8"/></svg>
        www.tomvarulek.net
      </li>
      <li>
        <svg class="contact-icon" viewBox="0 0 12 12" aria-hidden="true"><rect width="12" height="12" rx="2" fill="#4fe3c6"/><rect x="2.5" y="3.5" width="7" height="5" fill="none" stroke="#0d0d0e" stroke-width="1"/><path d="M2.5 3.5 6 6.5l3.5-3" fill="none" stroke="#0d0d0e" stroke-width="1"/></svg>
        tomvarulek@quillbox.net
      </li>
    </ul>
  </section>
  <section class="card card-front" aria-label="Card front with name">
    <div class="front-ring"></div>
    <div class="front-name">Tom Varulek</div>
  </section>
</main>
</body>
</html>
```